New Business Card Design Project

Use the flyer uploaded and website www.brightoakbuilders.com for inspiration.
List Our Services on Backside of business cards
Marcus Delling
Harborline Builders Inc.
Licensed General Contractors
858-471-6093

Contact Information for Business Card

Use the flyer uploaded and website www.brightoakbuilders.com for inspiration. List Our Services on Backside of business cards Marcus Delling Harborline Builders Inc. Licensed General Contractors 858-471-6093

```html
<!DOCTYPE html>
<html lang="en">
<head>
<meta charset="utf-8">
<title>Harborline Builders – Business Card</title>
<link href="https://fonts.googleapis.com/css2?family=Montserrat:wght@400;500;600;700&display=swap" rel="stylesheet">
<style>
  :root {
    --backdrop: #e9e4dc;
    --card: #171717;
    --ink: #ffffff;
    --ink-soft: #e6e6e6;
    --rule: #d9d9d9;
  }
  * { margin: 0; padding: 0; box-sizing: border-box; }
  html, body { width: 900px; height: 1200px; overflow: hidden; }
  body {
    position: relative;
    background: var(--backdrop);
    font-family: "Montserrat", sans-serif;
    color: var(--ink);
  }
  .card {
    position: absolute;
    left: 80px;
    width: 742px;
    height: 440px;
    background: var(--card);
    border-radius: 24px;
    box-shadow: 0 6px 18px rgba(0,0,0,0.25);
    overflow: hidden;
  }
  .card--front { top: 131px; }
  .card--back { top: 638px; }

  /* Front: services */
  .brand-name {
    position: absolute;
    font-weight: 400;
    letter-spacing: 2px;
    text-transform: uppercase;
    color: var(--ink);
    white-space: nowrap;
  }
  .card--front .brand-name {
    left: 40px;
    width: 300px;
    top: 268px;
    text-align: center;
    font-size: 20px;
  }
  .divider {
    position: absolute;
    left: 357px;
    top: 109px;
    width: 2px;
    height: 262px;
    background: var(--rule);
  }
  .services {
    position: absolute;
    left: 385px;
    top: 104px;
  }
  .services__title {
    font-size: 22px;
    font-weight: 600;
    margin-bottom: 10px;
  }
  .services__list { list-style: none; }
  .services__list li {
    font-size: 16.5px;
    font-weight: 400;
    color: var(--ink-soft);
    line-height: 26.5px;
    padding-left: 13px;
    position: relative;
  }
  .services__list li::before {
    content: "";
    position: absolute;
    left: 0;
    top: 10px;
    width: 6px;
    height: 6px;
    border-radius: 50%;
    background: var(--ink);
  }

  /* Back: contact */
  .card--back .brand-name {
    left: 30px;
    top: 52px;
    font-size: 24px;
  }
  .person {
    position: absolute;
    right: 44px;
    top: 50px;
    text-align: right;
  }
  .person__name { font-size: 25px; font-weight: 700; line-height: 30px; }
  .person__role { font-size: 15.5px; font-weight: 400; color: var(--ink-soft); margin-top: 2px; }
  .accent-bar {
    position: absolute;
    right: 0;
    top: 52px;
    width: 16px;
    height: 48px;
    background: var(--ink);
  }
  .address {
    position: absolute;
    left: 30px;
    top: 247px;
    font-size: 16px;
    line-height: 20px;
    color: var(--ink-soft);
  }
  .contacts {
    position: absolute;
    left: 30px;
    top: 328px;
    list-style: none;
  }
  .contacts li {
    display: flex;
    align-items: center;
    font-size: 15.5px;
    color: var(--ink-soft);
    height: 29px;
  }
  .contacts svg { width: 14px; height: 14px; margin-right: 16px; fill: var(--ink); }
</style>
</head>
<body>

  <section class="card card--front" aria-label="Business card front">
    <div class="brand-name">Harborline Builders</div>
    <div class="divider"></div>
    <div class="services">
      <h2 class="services__title">Our Services</h2>
      <ul class="services__list">
        <li>Remodel: Kitchen &amp; Bath</li>
        <li>Painting: Interior &amp; Exterior</li>
        <li>Flooring: Carpet, Vinyl, Wood</li>
        <li>Window &amp; Door Replacement</li>
        <li>Plumbing: Repair &amp; Upgrades</li>
        <li>Energy Efficienct Upgrades</li>
        <li>Deck &amp; Patio construction</li>
        <li>Water &amp; Mold Damage</li>
        <li>Garage Renovation</li>
      </ul>
    </div>
  </section>

  <section class="card card--back" aria-label="Business card back">
    <div class="brand-name">Harborline Builders</div>
    <div class="person">
      <div class="person__name">Marcus Delling</div>
      <div class="person__role">Licensed General Contractors</div>
    </div>
    <div class="accent-bar"></div>

    <address class="address" style="font-style:normal">
      240 Marlow Avenue, suite 305<br>
      Hartfield PA 18420
    </address>

    <ul class="contacts">
      <li>
        <svg viewBox="0 0 16 16" aria-hidden="true"><path d="M3 1h3l1.5 4-2 1.3a9 9 0 0 0 4.2 4.2L11 8.5l4 1.5v3a2 2 0 0 1-2 2A12 12 0 0 1 1 3a2 2 0 0 1 2-2z"/></svg>
        858-471-6093
      </li>
      <li>
        <svg viewBox="0 0 16 16" aria-hidden="true"><path d="M1 3h14v1.2L8 8.7 1 4.2z"/><path d="M1 5.6l7 4.5 7-4.5V13H1z"/></svg>
        info@brightoakbuilders.com
      </li>
      <li>
        <svg viewBox="0 0 16 16" aria-hidden="true"><circle cx="8" cy="8" r="7"/><path d="M1 8h14M8 1c3 3.5 3 10.5 0 14M8 1c-3 3.5-3 10.5 0 14" stroke="#171717" stroke-width="1.2" fill="none"/></svg>
        www.brightoakbuilders.com
      </li>
    </ul>
  </section>

</body>
</html>
```